Harborline Auto LLC

Car Dealer Customer Service
Address: 2874 Cresthaven Road, Marlowe Falls, ZX 00481
web: www.harborlineautoxq.net
email: harborlineautoxq@mailnest.example
Phone: (555) 555-0148
Phone: (555) 555-0173

```html
<!DOCTYPE html>
<html lang="en">
<head>
<meta charset="utf-8">
<title>Harborline Auto – Business Card</title>
<link href="https://fonts.googleapis.com/css2?family=Poppins:wght@600;700&family=Oswald:wght@500&family=Arimo:wght@400&display=swap" rel="stylesheet">
<style>
  :root {
    --stage: #1c1c1e;
    --card: #111112;
    --blue: #2a8fd0;
    --gold: #f2b23a;
    --white: #f4f4f4;
    --rule: #8a8a8a;
  }
  * { box-sizing: border-box; margin: 0; padding: 0; }
  html, body { width: 1200px; height: 900px; overflow: hidden; }
  body {
    background: var(--stage);
    display: flex;
    flex-direction: column;
    align-items: center;
    justify-content: center;
    gap: 40px;
  }
  .card {
    position: relative;
    width: 700px;
    height: 400px;
    background: var(--card);
    box-shadow: 0 10px 30px rgba(0,0,0,.6);
    overflow: hidden;
  }
  .card__band {
    position: absolute;
    left: 0; right: 0; bottom: 0;
    height: 14px;
    background: var(--blue);
  }

  /* Front */
  .front {
    display: flex;
    flex-direction: column;
    align-items: center;
    justify-content: center;
    padding-bottom: 30px;
  }
  .brand {
    display: flex;
    align-items: center;
    gap: 16px;
  }
  .brand__dot {
    width: 34px; height: 34px;
    border-radius: 50%;
    background: var(--blue);
  }
  .brand__name {
    font-family: "Poppins", sans-serif;
    font-weight: 700;
    font-size: 52px;
    letter-spacing: 2px;
    color: var(--blue);
    text-transform: uppercase;
    white-space: nowrap;
  }
  .tagline {
    margin-top: 8px;
    font-family: "Poppins", sans-serif;
    font-weight: 600;
    font-size: 22px;
    letter-spacing: 3px;
    color: var(--gold);
    text-transform: uppercase;
  }

  /* Back */
  .back { padding: 118px 20px 0 28px; }
  .back__top {
    display: flex;
    align-items: flex-start;
  }
  .person {
    width: 272px;
    flex: none;
    text-align: right;
    padding-right: 18px;
    padding-top: 4px;
  }
  .person__name {
    font-family: "Oswald", sans-serif;
    font-weight: 500;
    font-size: 36px;
    line-height: 1;
    color: var(--blue);
    text-transform: uppercase;
    letter-spacing: -.5px;
    white-space: nowrap;
  }
  .person__title {
    margin-top: 4px;
    font-family: "Arimo", sans-serif;
    font-size: 19px;
    color: var(--white);
    white-space: nowrap;
  }
  .divider {
    width: 1px;
    height: 120px;
    flex: none;
    background: var(--rule);
  }
  .contacts {
    list-style: none;
    padding-left: 18px;
    padding-top: 8px;
    font-family: "Arimo", sans-serif;
    font-size: 18px;
    color: var(--white);
  }
  .contacts li {
    display: flex;
    align-items: center;
    gap: 8px;
    line-height: 1.4;
    white-space: nowrap;
  }
  .contacts svg, .address svg { width: 18px; height: 18px; flex: none; fill: var(--blue); }
  .accent { color: var(--blue); }
  .address {
    position: absolute;
    left: 80px;
    bottom: 48px;
    display: flex;
    align-items: center;
    gap: 8px;
    font-family: "Arimo", sans-serif;
    font-size: 21px;
    color: var(--white);
    white-space: nowrap;
  }
</style>
</head>
<body>

  <section class="card front">
    <div class="brand">
      <span class="brand__dot"></span>
      <span class="brand__name">Harborline Auto</span>
    </div>
    <p class="tagline">Car Dealer Customer Service</p>
    <div class="card__band"></div>
  </section>

  <section class="card back">
    <div class="back__top">
      <div class="person">
        <h1 class="person__name">Marcus Delaney</h1>
        <p class="person__title">Managing Director</p>
      </div>
      <div class="divider"></div>
      <ul class="contacts">
        <li>
          <svg viewBox="0 0 24 24" aria-hidden="true"><path d="M6.6 10.8a15.1 15.1 0 0 0 6.6 6.6l2.2-2.2a1 1 0 0 1 1-.25 11.4 11.4 0 0 0 3.6.57 1 1 0 0 1 1 1V20a1 1 0 0 1-1 1A17 17 0 0 1 3 4a1 1 0 0 1 1-1h3.5a1 1 0 0 1 1 1c0 1.25.2 2.450.57 3.6a1 1 0 0 1-.25 1z"/></svg>
          (555) 555-0148
        </li>
        <li>
          <svg viewBox="0 0 24 24" aria-hidden="true"><path d="M6.6 10.8a15.1 15.1 0 0 0 6.6 6.6l2.2-2.2a1 1 0 0 1 1-.25 11.4 11.4 0 0 0 3.6.57 1 1 0 0 1 1 1V20a1 1 0 0 1-1 1A17 17 0 0 1 3 4a1 1 0 0 1 1-1h3.5a1 1 0 0 1 1 1c0 1.25.2 2.45.57 3.6a1 1 0 0 1-.25 1z"/></svg>
          (555) 555-0173
        </li>
        <li>
          <svg viewBox="0 0 24 24" aria-hidden="true"><path d="M12 2a10 10 0 1 0 0 20 10 10 0 0 0 0-20zm6.9 6h-2.9a15.6 15.6 0 0 0-1.4-3.6A8 8 0 0 1 18.9 8zM12 4a14 14 0 0 1 1.9 4h-3.8A14 14 0 0 1 12 4zM4.3 14a8 8 0 0 1 0-4h3.4a16.5 16.5 0 0 0 0 4zm.8 2h2.9a15.6 15.6 0 0 0 1.4 3.6A8 8 0 0 1 5.1 16zM8 8H5.1a8 8 0 0 1 4.3-3.6A15.6 15.6 0 0 0 8 8zm4 12a14 14 0 0 1-1.9-4h3.8A14 14 0 0 1 12 20zm2.3-6H9.7a14.7 14.7 0 0 1 0-4h4.6a14.7 14.7 0 0 1 0 4zm.3 5.6a15.6 15.6 0 0 0 1.4-3.6h2.9a8 8 0 0 1-4.3 3.6zM16.3 14a16.5 16.5 0 0 0 0-4h3.4a8 8 0 0 1 0 4z"/></svg>
          <span>www.<span class="accent">harborlineautoxq</span>.net</span>
        </li>
        <li>
          <svg viewBox="0 0 24 24" aria-hidden="true"><path d="M2 5h20v14H2zm2 2v.5l8 5 8-5V7zm0 2.8V17h16V9.8l-8 5z"/></svg>
          harborlineautoxq@mailnest.example
        </li>
      </ul>
    </div>
    <p class="address">
      <svg viewBox="0 0 24 24" aria-hidden="true"><path d="M12 2a7 7 0 0 0-7 7c0 5 7 13 7 13s7-8 7-13a7 7 0 0 0-7-7zm0 9.5A2.5 2.5 0 1 1 12 6.5a2.5 2.5 0 0 1 0 5z"/></svg>
      2874 Cresthaven Road, Marlowe Falls, ZX 00481
    </p>
    <div class="card__band"></div>
  </section>

</body>
</html>
```